Business card for event manager / organizer "waiter service"

Draft of a new valuable business card for my company.
Events, personnel service providers, festivals

```html
<!DOCTYPE html>
<html lang="de">
<head>
<meta charset="utf-8">
<title>Nils' Kellnerservice – Visitenkarte</title>
<link href="https://fonts.googleapis.com/css2?family=Lato:wght@400;700&display=swap" rel="stylesheet">
<style>
  :root {
    --bg: #2b2e38;
    --paper: #ffffff;
    --orange: #e8761c;
    --text-grey: #555a60;
    --brand-dark: #1c1c1c;
  }
  * { margin: 0; padding: 0; box-sizing: border-box; }
  html, body { width: 1200px; height: 800px; overflow: hidden; }
  body {
    background: var(--bg);
    font-family: 'Lato', sans-serif;
    position: relative;
  }
  .card {
    position: absolute;
    left: 320px;
    width: 560px;
    height: 320px;
    overflow: hidden;
  }
  .card-front { top: 50px; background: var(--paper); }
  .card-back { top: 430px; }

  .front-photo {
    position: absolute;
    right: 0; top: 0;
    width: 330px; height: 320px;
    background:
      radial-gradient(ellipse at 55% 85%, rgba(226,150,80,0.75) 0%, rgba(226,150,80,0) 55%),
      radial-gradient(ellipse at 60% 10%, rgba(150,150,230,0.8) 0%, rgba(150,150,230,0) 60%),
      linear-gradient(180deg, #b8b7e0 0%, #d9c9c0 55%, #d49a62 100%);
    -webkit-mask-image: linear-gradient(90deg, transparent 0%, #000 28%);
    mask-image: linear-gradient(90deg, transparent 0%, #000 28%);
  }

  .brand {
    position: absolute;
    left: 29px; top: 28px;
    display: flex; align-items: center; gap: 10px;
  }
  .brand-mark {
    width: 70px; height: 70px;
    background: var(--orange);
  }
  .brand-name {
    font-weight: 700;
    font-size: 36px;
    line-height: 1;
    color: var(--brand-dark);
    letter-spacing: 0.5px;
  }
  .brand-name small {
    display: block;
    font-size: 16px;
    margin-top: 4px;
  }
  .tagline {
    position: absolute;
    left: 88px; top: 106px;
    font-size: 8.5px;
    color: var(--text-grey);
    white-space: nowrap;
  }

  .person { position: absolute; left: 29px; top: 137px; }
  .person-name {
    font-size: 21px; font-weight: 700;
    color: var(--orange);
    letter-spacing: 0.3px;
  }
  .person-role { font-size: 14.5px; color: var(--text-grey); margin-top: 0; }

  .contact-list {
    position: absolute; left: 29px; top: 190px;
    list-style: none;
  }
  .contact-list li {
    display: flex; align-items: center; gap: 7px;
    font-size: 14.5px; color: var(--text-grey);
    height: 17.8px;
    white-space: nowrap;
  }
  .contact-list svg { width: 12px; height: 12px; flex: none; }

  .back-photo {
    width: 100%; height: 100%;
    background:
      linear-gradient(180deg, rgba(0,0,0,0) 82%, #8a6a46 88%, #5b4330 100%),
      linear-gradient(90deg, rgba(190,230,210,0.35) 5%, rgba(250,180,150,0.35) 30%, rgba(170,220,120,0.35) 48%, rgba(200,200,230,0.35) 66%, rgba(250,170,160,0.35) 86%),
      radial-gradient(ellipse at 50% 40%, #3a3f5a 0%, #1d2030 70%);
  }
</style>
</head>
<body>
  <section class="card card-front">
    <div class="front-photo" role="img" aria-label="Foto eines Brautpaares beim Einzug mit Konfetti und Funkenfontänen"></div>

    <div class="brand">
      <div class="brand-mark"></div>
      <div class="brand-name">NILS' <small>KELLNERSERVICE</small></div>
    </div>
    <p class="tagline">…weil jede Feier gute Gastgeber braucht!</p>

    <div class="person">
      <p class="person-name">NILS BERGMANN</p>
      <p class="person-role">Inhaber</p>
    </div>

    <ul class="contact-list">
      <li>
        <svg viewBox="0 0 24 24"><path fill="var(--orange)" d="M6.6 10.8a15 15 0 0 0 6.6 6.6l2.2-2.2a1 1 0 0 1 1-.25 11.4 11.4 0 0 0 3.6.6 1 1 0 0 1 1 1V20a1 1 0 0 1-1 1A17 17 0 0 1 3 4a1 1 0 0 1 1-1h3.5a1 1 0 0 1 1 1c0 1.250.2 2.450.6 3.6a1 1 0 0 1-.25 1z"/></svg>
        023 45 678 90 12
      </li>
      <li>
        <svg viewBox="0 0 24 24"><rect x="6" y="2" width="12" height="20" rx="2" fill="none" stroke="var(--orange)" stroke-width="2.2"/><circle cx="12" cy="18" r="1.3" fill="var(--orange)"/></svg>
        0170 123 45 67
      </li>
      <li>
        <svg viewBox="0 0 24 24"><rect x="2" y="2" width="20" height="20" rx="3" fill="var(--orange)"/></svg>
        /nilskellnerservice
      </li>
      <li>
        <svg viewBox="0 0 24 24"><rect x="2" y="5" width="20" height="14" fill="var(--orange)"/><path d="M2 5l10 8 10-8" fill="none" stroke="#fff" stroke-width="1.8"/></svg>
        info@nils-kellnerservice.de
      </li>
      <li>
        <svg viewBox="0 0 24 24" fill="none" stroke="var(--orange)" stroke-width="2"><circle cx="12" cy="12" r="10"/><ellipse cx="12" cy="12" rx="4.5" ry="10"/><path d="M2 12h20M4 7h16M4 17h16"/></svg>
        www.nils-kellnerservice.de
      </li>
      <li>
        <svg viewBox="0 0 24 24"><path fill="none" stroke="var(--orange)" stroke-width="2.2" d="M12 22s7-7.5 7-13a7 7 0 0 0-14 0c0 5.5 7 13 7 13z"/><circle cx="12" cy="9" r="2.5" fill="var(--orange)"/></svg>
        Birkenweg 12, 45000 Musterstadt
      </li>
    </ul>
  </section>

  <section class="card card-back">
    <div class="back-photo" role="img" aria-label="Foto von fünf bunten Cocktails in Weingläsern auf einer Holztheke"></div>
  </section>
</body>
</html>
```